Brindle Healthcare Coming Soon Sign

I need a large (10 x5) road banner announcing the construction of our new medical practice at 5187 Larkmoor Road in John's Island. The name of our practice is Brindle Healthcare and we thought it would be fund to nick name it the "Brindle Waystation". We'd like the tagline to read - "There's nothing healthy about driving an hour to see your doctor. So we're coming to you." Opening Late 2025 I have attached three logos as we have two other practices (Brindle Urgent and Brindle Aesthetics ) that should be present on the bottom of the sign but the main business is Brindle Healthcare. For more information on our look/feel visit our website www.goplainway-example.com (which should be somewhere on the banner as well)
Updates

The signage needs to say Coming Late Fall 2025!

Target Market(s)

Drive By traffic must be made aware that we are coming soon

Industry/Entity Type

Healthcare

Requirements
Nice to have
• Western Theme

```html
<!DOCTYPE html>
<html lang="en">
<head>
<meta charset="utf-8">
<title>Brindle Healthcare – Coming Late Fall 2025 Banner</title>
<link rel="stylesheet" href="https://fonts.googleapis.com/css2?family=Roboto:ital,wght@0,500;0,700;1,400;1,500&family=Montserrat:wght@600&family=Crimson+Text:ital@1&display=swap">
<style>
  :root {
    --page: #e9eaec;
    --gold: #e8a93a;
    --gold-soft: #d9b15e;
    --slate: #5d6f8c;
    --sky: #9fb0c4;
    --navy: #1d355d;
    --red: #e8443a;
    --white: #ffffff;
    --shirt: #f1eee9;
    --dress: #26396d;
    --skin: #d9b9a0;
    --brand-blue: #5aaee8;
    --brand-pink: #f0468a;
    --brand-red: #ee3f3a;
    --shadow: rgba(90, 55, 20, 0.55);
  }
  * { box-sizing: border-box; margin: 0; padding: 0; }
  html, body {
    width: 1118px; height: 1200px; overflow: hidden;
    background: var(--page);
  }
  .banner {
    position: absolute; left: 0; top: 320px;
    width: 1118px; height: 559px; overflow: hidden;
    background: var(--gold);
  }
  .street-scene {
    position: absolute; inset: 0;
    background:
      linear-gradient(180deg, rgba(232,169,58,0) 55%, var(--gold) 100%),
      linear-gradient(100deg, var(--gold-soft) 0%, #c9a866 35%, var(--sky) 62%, var(--slate) 100%);
  }
  .headline-new {
    position: absolute; left: 68px; top: 14px;
    font: 700 268px/1 "Roboto", sans-serif;
    letter-spacing: -6px;
    color: var(--white);
    text-shadow: 4px 4px 3px var(--shadow);
  }
  .headline-practice {
    position: absolute; left: 56px; top: 264px;
    font: 500 62px/1 "Roboto", sans-serif;
    color: var(--white);
    text-shadow: 3px 3px 2px var(--shadow);
    white-space: nowrap;
  }
  .opening-pill {
    position: absolute; left: 81px; top: 339px;
    width: 519px; height: 67px; border-radius: 34px;
    background: var(--red);
    display: flex; align-items: center; justify-content: center;
    font: 700 38px/1 "Roboto", sans-serif;
    color: var(--white);
    text-shadow: 2px 2px 2px rgba(0,0,0,0.25);
    white-space: nowrap;
  }
  .tagline-band {
    position: absolute; left: 0; top: 436px;
    width: 1118px; height: 90px;
    background: var(--navy);
  }
  .tagline {
    position: absolute; left: 0; top: 445px; width: 682px;
    text-align: center;
    font: italic 400 24.5px/37px "Crimson Text", serif;
    color: var(--white);
  }
  .doctor-visit {
    position: absolute; left: 672px; top: 232px;
    width: 446px; height: 327px;
    border-radius: 90px 140px 0 0;
    background:
      linear-gradient(180deg, rgba(217,185,160,0.9) 0%, rgba(217,185,160,0) 30%),
      linear-gradient(90deg, var(--shirt) 0%, var(--shirt) 38%, #b9bfcc 48%, var(--dress) 58%, var(--dress) 100%);
  }
  .brand-row {
    position: absolute; top: 30px; left: 684px; right: 22px;
    display: flex; justify-content: space-between;
  }
  .brand {
    display: flex; align-items: center; gap: 7px;
    font: 600 12px/1.3 "Montserrat", sans-serif;
    letter-spacing: 1.6px; text-transform: uppercase;
  }
  .brand-mark { width: 22px; height: 22px; border-radius: 4px; flex: none; }
  .brand--healthcare { color: var(--brand-blue); }
  .brand--healthcare .brand-mark { background: var(--brand-blue); }
  .brand--aesthetics { color: var(--brand-pink); }
  .brand--aesthetics .brand-mark { background: var(--brand-pink); border-radius: 50%; }
  .brand--urgent { color: var(--brand-red); }
  .brand--urgent .brand-mark { background: var(--brand-red); }
  .contact {
    position: absolute; right: 30px;
    display: flex; align-items: center; gap: 8px;
    font: italic 500 26px/1 "Roboto", sans-serif;
    color: var(--white);
    white-space: nowrap;
  }
  .contact--web { top: 113px; }
  .contact--phone { top: 163px; font-size: 32px; }
  .contact svg { flex: none; }
</style>
</head>
<body>
  <section class="banner" aria-label="Brindle Healthcare coming soon road banner">
    <div class="street-scene" role="img" aria-label="Street view of the new practice building with porches, palm trees and greenery"></div>

    <div class="headline-new">NEW</div>
    <div class="headline-practice">MEDICAL PRACTICE</div>
    <div class="opening-pill">COMING LATE FALL 2025!</div>

    <div class="tagline-band"></div>
    <p class="tagline">There's nothing healthy about driving an hour to see your doctor.<br>So We're coming to you.</p>

    <div class="doctor-visit" role="img" aria-label="Doctor in a white shirt listening to a young girl's heartbeat with a stethoscope"></div>

    <div class="brand-row">
      <div class="brand brand--healthcare"><span class="brand-mark"></span><span>Brindle<br>Healthcare</span></div>
      <div class="brand brand--aesthetics"><span class="brand-mark"></span><span>Brindle<br>Aesthetics</span></div>
      <div class="brand brand--urgent"><span class="brand-mark"></span><span>Brindle<br>Urgent</span></div>
    </div>

    <div class="contact contact--web">
      <svg width="34" height="34" viewBox="0 0 34 34" fill="none" stroke="#fff" stroke-width="2.4" aria-hidden="true">
        <circle cx="17" cy="17" r="15"/>
        <ellipse cx="17" cy="17" rx="7" ry="15"/>
        <line x1="2" y1="17" x2="32" y2="17"/>
        <path d="M5 9h24M5 25h24"/>
      </svg>
      <span>www.goplainway-example.com</span>
    </div>
    <div class="contact contact--phone">
      <svg width="26" height="34" viewBox="0 0 26 34" fill="none" stroke="#fff" stroke-width="2.4" aria-hidden="true">
        <path d="M8 3l5 7-3 3c1 4 3 8 6 11l3-2 6 5-4 5C11 30 3 18 3 7z"/>
      </svg>
      <span>(843) 555-0142</span>
    </div>
  </section>
</body>
</html>
```